Sophisticated, clean website reflecting my feminine, playful side to sell my abstract art,

I need a website no more than 3 pages to showcase my paintings, a little about me and some contact info. I do abstracts so looking for something a little edgy, yet feminine and current.
Updates

Hi there, These are some artists websites that I Iike: Marnelvoss.com (I like how airy it is) peterwallombry.com garethpolvens.com (I like how it scrolls) I'll need a place for a photo ( a headshot-i do not have it yet so I'll need to be able to upload that later) as well as an area for my bio. Also, it's important that I will be able to upload any new photos and descriptions easily so it should be user friendly. Lastly, I like in a sunny place so would like to have this seem upbeat and playful as that is how i like to paint. thanks-I'm trying to upload my photos now -

Target Market(s)

ppl ages 35-70 who want large scale art for their homes

Industry/Entity Type

art

Coding

Coded - Design and coding required

Number of Pages Required

3 page

Colors

Designer to choose colors to be used in the design.

Requirements
Must have
• photos of my art, a place for my bio, be easy to reach me. tasteful-nothing too "in your face" -my clients are pretty high end and organized. They like clean lines
Nice to have
• sophisticated background, muted tones in the back-similar clean font throughout-no cursive
Should not have
• too many dark areas. Too many blocks of color. Too serious.

```html
<!DOCTYPE html>
<html lang="en">
<head>
<meta charset="utf-8">
<title>Hazel Stenmark Art</title>
<link href="https://fonts.googleapis.com/css2?family=Mulish:wght@400;500;600;700;800;900&display=swap" rel="stylesheet">
<style>
:root{
  --blue:#0a6cb8;
  --ink:#111111;
  --text:#2b2b2b;
  --white:#ffffff;
  --sky:#eaf5fc;
  --label:#3a3a3a;
  --line:#1a1a1a;
  --footer:#0d0d0d;
}
*{box-sizing:border-box;margin:0;padding:0}
html,body{width:1200px;height:2836px;overflow:hidden;background:var(--white)}
body{position:relative;font-family:"Mulish",sans-serif;color:var(--text)}
.abs{position:absolute}

/* hero */
.hero{position:absolute;left:0;top:0;width:1200px;height:690px;overflow:hidden}
.hero-art{position:absolute;inset:0;
  background:
   radial-gradient(circle at 62% 52%, #5a2a1c 0 40px, transparent 90px),
   radial-gradient(circle at 30% 40%, #a04a28 0 60px, transparent 180px),
   radial-gradient(circle at 80% 25%, #b0532e 0 40px, transparent 170px),
   radial-gradient(circle at 15% 75%, #c78aa8 0 60px, transparent 220px),
   radial-gradient(circle at 70% 80%, #d6a0b8 0 50px, transparent 220px),
   linear-gradient(135deg,#c99aab,#b46a5a 40%,#d8b0c2 70%,#a65a3e);}
.hero-fade{position:absolute;left:0;right:0;bottom:0;height:170px;background:linear-gradient(to bottom,rgba(255,255,255,0),#ffffff)}
.brand{position:absolute;left:131px;top:20px;font-size:26px;font-weight:800;color:var(--white)}
.nav{position:absolute;right:135px;top:23px;display:flex;gap:40px;font-size:15px;font-weight:700;color:var(--white)}
.hero-title{position:absolute;left:0;width:1200px;top:245px;text-align:center;font-size:50px;font-weight:900;color:var(--white);text-shadow:0 2px 8px rgba(0,0,0,.35)}
.hero-sub{position:absolute;left:0;width:1200px;top:313px;text-align:center;font-size:22px;font-weight:700;color:var(--white);text-shadow:0 2px 6px rgba(0,0,0,.35)}
.dots{position:absolute;top:601px;left:0;width:1200px;display:flex;justify-content:center;gap:7px}
.dots span{width:10px;height:10px;border-radius:50%;background:var(--white)}
.dots span.on{background:var(--blue)}

/* section heading with double frame */
.heading{position:absolute;height:42px;border:1px solid var(--line);padding:3px}
.heading div{height:100%;border:1px solid var(--line);display:flex;align-items:center;justify-content:center;font-size:22px;font-weight:800;color:var(--ink);background:var(--white)}
.heading b{color:var(--blue);font-weight:800;margin-left:6px}

/* paintings */
.card{position:absolute;width:295px;height:351px;border:1px solid var(--line)}
.card::after{content:"";position:absolute;left:3px;top:3px;right:3px;bottom:3px;border:1px solid var(--line)}
.card .art{position:absolute;left:9px;top:9px;right:14px;bottom:14px}
.card .tag{position:absolute;left:50%;transform:translateX(-50%);bottom:14px;background:var(--label);color:var(--white);font-size:14px;font-weight:800;padding:7px 16px;white-space:nowrap;z-index:2}
.btn{position:absolute;background:var(--blue);color:var(--white);font-size:15px;font-weight:800;display:flex;align-items:center;justify-content:center}

/* about */
.about{position:absolute;left:0;top:1669px;width:1200px;height:468px;background:var(--sky)}
.portrait{position:absolute;left:131px;top:1713px;width:376px;height:376px;border-radius:50%;background:radial-gradient(circle at 50% 40%,#c9704a 0 70px,#6c7fb0 140px,#dcdcdc 190px)}
.bio{position:absolute;left:578px;top:1803px;width:468px;font-size:15px;line-height:23.2px;text-align:justify;color:#333}

/* contact */
.contact{position:absolute;left:0;top:2137px;width:1200px;height:537px;
  background:linear-gradient(90deg,#6f7fa5 0 300px,#d7cbb4 300px 470px,#0f7f7a 470px 870px,#d1c3a8 870px 1000px,#1d3270 1000px)}
.panel{position:absolute;left:203px;top:2266px;width:794px;height:354px;background:rgba(255,255,255,.94)}
.col-title{position:absolute;font-size:19px;font-weight:800;color:var(--ink)}
.info{position:absolute;left:275px;font-size:13.5px;line-height:19px;color:#333}
.icon{position:absolute;left:240px;width:23px;height:23px}
.field{position:absolute;border:1px solid #8a8a8a;background:var(--white);font-size:11px;color:#333;padding:12px 14px}

/* footer */
.footer{position:absolute;left:0;top:2674px;width:1200px;height:162px;background:var(--footer);color:var(--white)}
.f-brand{position:absolute;left:131px;top:34px;font-size:23px;font-weight:800}
.f-nav{position:absolute;right:137px;top:40px;display:flex;gap:38px;font-size:15px;font-weight:500}
.f-rule{position:absolute;left:131px;right:135px;top:84px;height:1px;background:#444}
.follow{position:absolute;left:131px;top:111px;display:flex;align-items:center;gap:16px;font-size:11px}
.social{display:flex;align-items:center;gap:6px;font-size:11px}
.social i{width:12px;height:12px;border-radius:50%;background:var(--blue);display:block}
.copy{position:absolute;right:137px;top:116px;font-size:12px}
</style>
</head>
<body>

<header class="hero">
  <div class="hero-art" role="img" aria-label="Close-up of an abstract painting with rust, pink and violet brushstrokes"></div>
  <div class="hero-fade"></div>
  <div class="brand">Hazel Stenmark Art</div>
  <nav class="nav"><span>PAINTINGS</span><span>ABOUT ME</span><span>CONTACT ME</span></nav>
  <h1 class="hero-title">ABSTRACT PAINTINGS</h1>
  <p class="hero-sub">Lorem Ipsum is simply dummy text of the printing</p>
  <div class="dots"><span></span><span></span><span class="on"></span><span></span><span></span></div>
</header>

<section>
  <div class="heading" style="left:505px;top:733px;width:190px"><div>MY<b>PAINTINGS</b></div></div>

  <div class="card" style="left:130px;top:813px"><div class="art" role="img" aria-label="Abstract painting with purple floral bursts" style="background:radial-gradient(circle at 45% 45%,#5b3f86,#9a86b4 45%,#e6e0d8)"></div><span class="tag">PAINTING 1</span></div>
  <div class="card" style="left:452px;top:813px"><div class="art" role="img" aria-label="Abstract painting with rust swirls" style="background:radial-gradient(circle at 45% 55%,#6e2414,#b65a3a 40%,#eadfd8)"></div><span class="tag">PAINTING 2</span></div>
  <div class="card" style="left:772px;top:813px"><div class="art" role="img" aria-label="Abstract painting with green and teal strokes" style="background:linear-gradient(135deg,#e8e6e6,#3f9a4a 45%,#1e6b55 75%,#d9c46a)"></div><span class="tag">PAINTING 3</span></div>

  <div class="card" style="left:130px;top:1190px"><div class="art" role="img" aria-label="Abstract painting with yellow and blue spiral rings" style="background:radial-gradient(circle at 40% 40%,#c9a43a,#2d4f9a 40%,#efe9dc 75%)"></div><span class="tag">PAINTING 4</span></div>
  <div class="card" style="left:452px;top:1190px"><div class="art" role="img" aria-label="Abstract painting with blue paint drips" style="background:linear-gradient(to bottom,#e6e2dc 0 25%,#3f8fc2 40%,#b8d6e6 70%,#e9e7e3)"></div><span class="tag">PAINTING 5</span></div>
  <div class="card" style="left:772px;top:1190px"><div class="art" role="img" aria-label="Abstract painting with brown and pink roses" style="background:radial-gradient(circle at 60% 45%,#d9a9a8,#6b2e22 45%,#ece6e2 85%)"></div><span class="tag">PAINTING 6</span></div>

  <div class="btn" style="left:509px;top:1575px;width:183px;height:35px">VIEW ALL PAINTINGS</div>
</section>

<section class="about"></section>
<div class="portrait" role="img" aria-label="Portrait photo of the artist in her studio"></div>
<div class="heading" style="left:578px;top:1728px;width:160px"><div>ABOUT<b>ME</b></div></div>
<p class="bio">There are many variations of passages of Lorem Ipsum available, but the majority have suffered alteration in some form, by injected humour, or randomised words which don't look even slightly believable. If you are going to use a passage of Lorem Ipsum, you need to be sure there isn't anything embarrassing hidden in the middle of text. All the Lorem Ipsum generators on the Internet tend to repeat predefined chunks as necessary, making this the first true generator on the Internet. It uses a dictionary of over 200 Latin words, combined with a handful of model</p>
<div class="btn" style="left:580px;top:2039px;width:121px;height:35px">READ MORE</div>

<section class="contact" role="img" aria-label="Abstract painting background in slate blue, sand, teal and navy bands"></section>
<div class="heading" style="left:515px;top:2186px;width:170px"><div>CONTACT<b>ME</b></div></div>
<div class="panel"></div>

<div class="col-title" style="left:240px;top:2298px">CONTACT US</div>
<svg class="icon" style="top:2356px" viewBox="0 0 24 24"><circle cx="12" cy="12" r="12" fill="#0a6cb8"/><path d="M12 6a3.5 3.5 0 0 0-3.5 3.5C8.5 12 12 17 12 17s3.5-5 3.5-7.5A3.5 3.5 0 0 0 12 6z" fill="#fff"/><circle cx="12" cy="9.5" r="1.3" fill="#0a6cb8"/></svg>
<div class="info" style="top:2347px">418 Larkspur Ave 2nd Floor Suite 12<br>Cedar Bay, FL&nbsp; 32100</div>
<svg class="icon" style="top:2418px" viewBox="0 0 24 24"><circle cx="12" cy="12" r="12" fill="#0a6cb8"/><path d="M8.6 6.5l1.8 2.4-1 1.3a7 7 0 0 0 4.4 4.4l1.3-1 2.4 1.8-1 2c-4.8-.4-8.6-4.2-9-9z" fill="#fff"/></svg>
<div class="info" style="top:2409px">Call Us<br>+1 555 014 2290</div>
<svg class="icon" style="top:2479px" viewBox="0 0 24 24"><circle cx="12" cy="12" r="12" fill="#0a6cb8"/><rect x="6.5" y="8" width="11" height="8" rx="1" fill="#fff"/><path d="M6.8 8.4L12 12.5l5.2-4.1" fill="none" stroke="#0a6cb8" stroke-width="1.2"/></svg>
<div class="info" style="top:2470px">E mail Us<br>hello@hazelstenmark.com</div>

<div class="col-title" style="left:557px;top:2298px">SEND MESSAGE</div>
<div class="field" style="left:559px;top:2333px;width:198px;height:37px">FIRST NAME</div>
<div class="field" style="left:765px;top:2333px;width:198px;height:37px">LAST NAME</div>
<div class="field" style="left:559px;top:2380px;width:198px;height:37px">EMAIL ID</div>
<div class="field" style="left:765px;top:2380px;width:198px;height:37px">PHONE</div>
<div class="field" style="left:559px;top:2429px;width:404px;height:105px">MESSAGE</div>
<div class="btn" style="left:560px;top:2546px;width:87px;height:35px">SUBMIT</div>

<footer class="footer">
  <div class="f-brand">Hazel Stenmark Art</div>
  <nav class="f-nav"><span>PAINTINGS</span><span>ABOUT ME</span><span>CONTACT ME</span></nav>
  <div class="f-rule"></div>
  <div class="follow">
    <span>FOLLOW ME</span>
    <span class="social"><i></i>Snapfolio</span>
    <span class="social"><i></i>Friendwall</span>
    <span class="social"><i></i>Clipstream</span>
  </div>
  <div class="copy">Copyright © 2022 All Rights Reserved</div>
</footer>

</body>
</html>
```